Harborview Estates Business Card for Apartment Buildings

Create business cards for resident managers who run apartment buildings. The audience is the public who are searching for apartment rentals, and current residents who live at the apartment building. Key design element will be incorporating the company logo, however, the logo cannot dominate. The building name and manager name are more important than the logo. Current business card design leaves little room for copy, so we may need to reduce the size on the current card to allow for more space for copy.

Target Market(s)

Adults 18-65 years of age, who are looking for an apartment rental, plus current residents who live at our apartment buildings.

Industry/Entity Type

Property Management

Contact Information for Business Card

A major design element will be use of the company logo. Important property and manager contact information must be part of the design. The size of the logo will need to be reduced to make room for building and manager contact copy.

Font styles to use
Sans Serif

Colors
3176b5
000000
959595
ffffff

Requirements
Must have
• 1) Incorporate the company logo.
• 2) Use the company colors (dark blue, black/grey, over white).
• 3) FEATURE THE BUILDING NAME
• 4) FEATURE THE MANAGER NAME
• 5) The company name is less important than BUILDING and MANAGER
• 6) Manager contact information
• **SEE ATTACHED CREATIVE BRIEF**
Nice to have
• 1) Back of card logo watermark
• 2) Ability to write notes on back of carfd
Should not have
• Avoid letting the company logo dominate the card, the building name and manager are more important than the company logo.

```html
<!DOCTYPE html>
<html lang="en">
<head>
<meta charset="utf-8">
<title>Harborview Estates Business Card</title>
<link href="https://fonts.googleapis.com/css2?family=Roboto:wght@400;500;700&family=Roboto+Condensed:wght@700&display=swap" rel="stylesheet">
<style>
  :root {
    --brand-blue: #1f5f9a;
    --link-blue: #3176b5;
    --ink: #222222;
    --charcoal: #3a3d40;
    --grey: #959595;
    --paper: #ffffff;
    --backdrop: #e4e5e6;
  }
  * { box-sizing: border-box; margin: 0; padding: 0; }
  html, body { width: 1200px; height: 726px; overflow: hidden; }
  body {
    background: var(--backdrop);
    font-family: "Roboto", sans-serif;
    color: var(--ink);
    position: relative;
  }
  .card {
    position: absolute;
    top: 208px;
    width: 540px;
    height: 310px;
    background: var(--paper);
    box-shadow: 0 6px 18px rgba(0,0,0,0.12);
    overflow: hidden;
  }
  .card--front { left: 40px; }
  .card--back { left: 620px; }

  .wordmark { display: flex; align-items: center; gap: 10px; }
  .wordmark__mark { width: 34px; height: 34px; background: var(--brand-blue); }
  .wordmark__name {
    font-weight: 700;
    color: var(--brand-blue);
    line-height: 1.02;
    letter-spacing: 0.5px;
    text-transform: uppercase;
  }

  .card--front .wordmark {
    position: absolute; left: 50%; top: 112px; transform: translateX(-50%);
  }
  .card--front .wordmark__name { font-size: 30px; }
  .card--front .web {
    position: absolute; left: 0; right: 0; bottom: 40px;
    text-align: center; font-size: 15px; color: var(--ink);
  }
  .web span { color: var(--link-blue); }

  .card__swoosh { position: absolute; inset: 0; }

  .building {
    position: absolute; left: 26px; top: 26px; color: var(--paper);
  }
  .building__name {
    font-family: "Roboto Condensed", sans-serif;
    font-weight: 700; font-size: 22px; letter-spacing: 0.3px; text-transform: uppercase;
  }
  .building__label { font-size: 13px; margin-top: 3px; }

  .person {
    position: absolute; right: 26px; top: 26px; text-align: right; color: var(--paper);
  }
  .person__name {
    font-family: "Roboto Condensed", sans-serif;
    font-weight: 700; font-size: 26px; letter-spacing: 0.3px; text-transform: uppercase;
  }
  .person__title { font-size: 14px; margin-top: 2px; }

  .card--back .wordmark { position: absolute; left: 30px; top: 160px; gap: 8px; }
  .card--back .wordmark__mark { width: 22px; height: 22px; }
  .card--back .wordmark__name { font-size: 18px; }

  .contacts { position: absolute; left: 30px; bottom: 20px; list-style: none; }
  .contacts li {
    display: flex; align-items: center; gap: 9px;
    font-size: 13.5px; line-height: 19px; color: var(--ink);
  }
  .contacts svg { width: 13px; height: 13px; flex: none; }
  .address {
    position: absolute; right: 26px; top: 226px;
    font-size: 13.5px; line-height: 18px; text-align: right; font-style: normal;
  }
</style>
</head>
<body>
  <section class="card card--front" aria-label="Card front">
    <div class="wordmark">
      <span class="wordmark__mark"></span>
      <span class="wordmark__name">Harborview<br>Estates</span>
    </div>
    <p class="web">www.<span>harborviewestates</span>.us</p>
  </section>

  <section class="card card--back" aria-label="Card back">
    <svg class="card__swoosh" viewBox="0 0 540 310" preserveAspectRatio="none" aria-hidden="true">
      <path d="M0,0 H540 V96 C470,112 400,130 330,118 C250,104 170,112 0,140 Z" fill="var(--brand-blue)"/>
      <path d="M0,150 C150,118 240,112 320,126 C400,140 470,122 540,104 V114 C470,138 400,152 320,140 C230,126 140,132 0,172 Z" fill="var(--charcoal)"/>
    </svg>
    <div class="building">
      <p class="building__name">Linden Crest</p>
      <p class="building__label">Apartments</p>
    </div>
    <div class="person">
      <p class="person__name">Dana Whitfield</p>
      <p class="person__title">Property Manager</p>
    </div>
    <div class="wordmark">
      <span class="wordmark__mark"></span>
      <span class="wordmark__name">Harborview<br>Estates</span>
    </div>
    <address class="address">2750 Linden Crest Road<br>#B210 Fairview, CA 92140</address>
    <ul class="contacts">
      <li>
        <svg viewBox="0 0 16 16" aria-hidden="true"><circle cx="8" cy="8" r="7" fill="none" stroke="var(--brand-blue)" stroke-width="1.5"/><path d="M5 4.5c0 4 2.5 6.5 6.5 6.5l.5-1.6-2-.8-.8.9C8 8.9 7.1 8 6.5 6.8l.9-.8-.8-2z" fill="var(--brand-blue)"/></svg>
        555-014-2281
      </li>
      <li>
        <svg viewBox="0 0 16 16" aria-hidden="true"><rect x="4" y="1.5" width="8" height="4" fill="var(--brand-blue)"/><rect x="1.5" y="6" width="13" height="6" rx="1" fill="var(--brand-blue)"/><rect x="4" y="10" width="8" height="4.5" fill="var(--paper)" stroke="var(--brand-blue)"/></svg>
        555-014-3390
      </li>
      <li>
        <svg viewBox="0 0 16 16" aria-hidden="true"><rect x="1.5" y="3.5" width="13" height="9" fill="none" stroke="var(--brand-blue)" stroke-width="1.4"/><path d="M1.5 3.5 8 9l6.5-5.5" fill="none" stroke="var(--brand-blue)" stroke-width="1.4"/></svg>
        dana@harborviewestates.us
      </li>
      <li>
        <svg viewBox="0 0 16 16" aria-hidden="true"><circle cx="8" cy="8" r="6.5" fill="none" stroke="var(--brand-blue)" stroke-width="1.4"/><ellipse cx="8" cy="8" rx="3" ry="6.5" fill="none" stroke="var(--brand-blue)" stroke-width="1.2"/><path d="M1.5 8h13" stroke="var(--brand-blue)" stroke-width="1.2"/></svg>
        <span class="web">www.<span>harborviewestates</span>.us</span>
      </li>
    </ul>
  </section>
</body>
</html>
```